Elevating our current Business Card Design

We want to elevate our current business card with a new design to look like a zenith 300 company. We are a premium lubricant distributor (oil and grease).
We need 2 versions, version 1 is as per the uploaded a copy of our current business card with the English version.
For our Chinese version we need to use the front to be English in English and have the back of the card designed exactly like the front for all info to be in Chinese.
The design template needs to be such that we can amend the template with adding different information for each person's card.
The background colour of the card can be changed- we just need to clearly see all information on the card and logos.
The QJR and Ember steady logos cannot have any colour or display changes- only use the logos attached.
All logos need to be included and all information from the attached current card

```html
<!DOCTYPE html>
<html lang="en">
<head>
<meta charset="utf-8">
<title>Norvale – Business Card</title>
<link rel="stylesheet" href="https://fonts.googleapis.com/css2?family=Open+Sans:wght@400;600;700&display=swap">
<style>
  :root{
    --stage:#34383e;
    --card:#1f1f22;
    --red:#e8262a;
    --red-deep:#a8181d;
    --gold:#e0a526;
    --silver:#c9c9cc;
    --white:#ffffff;
    --orange:#f08a1c;
    --ghost:#2c2b2a;
  }
  *{box-sizing:border-box;margin:0;padding:0}
  html,body{width:1200px;height:780px;overflow:hidden}
  body{
    background:var(--stage);
    font-family:"Open Sans",Arial,sans-serif;
    color:var(--white);
    position:relative;
  }
  .card{
    position:absolute;
    width:540px;height:310px;
    background:var(--card);
    overflow:hidden;
    box-shadow:0 10px 24px rgba(0,0,0,.35);
  }
  .card--contact{left:30px;top:235px}
  .card--brand{left:630px;top:235px}

  /* contact side */
  .brand-word{
    font-family:"Open Sans",Arial,sans-serif;
    font-weight:700;
    color:var(--red);
    display:flex;align-items:center;gap:10px;
    letter-spacing:.5px;
  }
  .brand-word__dot{
    display:inline-block;border-radius:50%;background:var(--gold);
  }
  .card--contact .brand-word{position:absolute;left:200px;top:34px;font-size:40px}
  .card--contact .brand-word__dot{width:22px;height:22px}

  .address{
    position:absolute;left:36px;top:104px;
    font-size:13px;line-height:18px;
  }
  .contact-list{
    position:absolute;left:36px;top:150px;
    list-style:none;font-size:13px;line-height:21px;
  }
  .contact-list li{display:flex;align-items:center;gap:9px}
  .contact-list svg{width:12px;height:12px;flex:none}

  .emblem-ghost{
    position:absolute;right:40px;top:120px;
    width:230px;height:200px;
    background:radial-gradient(ellipse at 50% 55%, var(--ghost) 0%, rgba(44,43,42,.55) 50%, rgba(31,31,34,0) 72%);
  }
  .person{
    position:absolute;right:44px;top:196px;text-align:right;
  }
  .person__name{color:var(--red);font-weight:600;font-size:26px;line-height:30px}
  .person__role{font-size:14px;margin-top:2px}
  .edge-bar{
    position:absolute;right:0;top:220px;width:16px;height:70px;background:var(--red);
  }

  /* brand side */
  .card--brand .brand-word{
    position:absolute;left:0;right:0;top:78px;justify-content:center;font-size:64px;
  }
  .card--brand .brand-word__dot{width:34px;height:34px}
  .badge-row{
    position:absolute;left:22px;right:22px;bottom:22px;
    display:flex;align-items:center;gap:12px;
  }
  .badge{flex:none}
  .badge--member{width:38px;height:30px;border-radius:18px 18px 4px 4px;background:var(--silver)}
  .badge--cert{width:30px;height:30px;border-radius:50%;background:var(--orange);border:3px solid #6d6d70}
  .partner-box{
    display:flex;align-items:center;
    border:1.5px solid var(--red);height:38px;
  }
  .partner-box .brand-word{position:static;font-size:15px;padding:0 12px}
  .partner-box .brand-word__dot{width:9px;height:9px}
  .partner-tag{
    background:var(--red);height:100%;
    padding:3px 12px;display:flex;flex-direction:column;justify-content:center;
  }
  .partner-tag__name{font-weight:700;font-size:14px;line-height:16px}
  .partner-tag__line{font-size:7px;letter-spacing:.6px;line-height:10px}
</style>
</head>
<body>

<section class="card card--contact">
  <div class="brand-word"><span class="brand-word__dot"></span>Norvale</div>

  <p class="address">48 Freightway Drive<br>Carlin, WA 6190</p>

  <ul class="contact-list">
    <li><svg viewBox="0 0 12 12"><path d="M2.5 1l2 2.2-1 1.3a7 7 0 0 0 4 4l1.3-1 2.2 2-1.3 1.5C5.5 10.5 1.5 6.5 1 2.3z" fill="var(--red)"/></svg>1300 472 610</li>
    <li><svg viewBox="0 0 12 12"><rect x="3" y="0.8" width="6" height="10.4" rx="1" fill="none" stroke="var(--red)" stroke-width="1.3"/></svg>+61 400 218 734</li>
    <li><svg viewBox="0 0 12 12"><rect x="1" y="5" width="10" height="6" rx="1" fill="var(--red)"/><rect x="3" y="1" width="6" height="4" fill="none" stroke="var(--red)" stroke-width="1.2"/></svg>+61 8 9000 4127</li>
    <li><svg viewBox="0 0 12 12"><circle cx="6" cy="6" r="5" fill="none" stroke="var(--red)" stroke-width="1.3"/><path d="M1 6h10M6 1c2.5 2.5 2.5 7.5 0 10M6 1c-2.5 2.5-2.5 7.5 0 10" fill="none" stroke="var(--red)" stroke-width="1"/></svg>www.norvaledirect.com</li>
    <li><svg viewBox="0 0 12 12"><rect x="1" y="2.5" width="10" height="7" rx="1" fill="var(--red)"/><path d="M1.5 3l4.5 3.5L10.5 3" fill="none" stroke="var(--card)" stroke-width="1"/></svg>mara.holten@norvaledirect.com</li>
  </ul>

  <div class="emblem-ghost" role="img" aria-label="Faint brand emblem decoration"></div>

  <div class="person">
    <p class="person__name">Mara Holten</p>
    <p class="person__role">Administration Executive</p>
  </div>
  <div class="edge-bar"></div>
</section>

<section class="card card--brand">
  <div class="brand-word"><span class="brand-word__dot"></span>Norvale</div>

  <div class="badge-row">
    <span class="badge badge--member" role="img" aria-label="Ember steady network member badge"></span>
    <span class="badge badge--cert" role="img" aria-label="QJR certification badge"></span>
    <div class="partner-box">
      <div class="brand-word"><span class="brand-word__dot"></span>Norvale</div>
      <div class="partner-tag">
        <span class="partner-tag__name">Kestrel</span>
        <span class="partner-tag__line">PREMIUM LUBRICANTS</span>
      </div>
    </div>
    <span class="badge badge--cert" role="img" aria-label="QJR certification badge"></span>
    <span class="badge badge--cert" role="img" aria-label="QJR certification badge"></span>
  </div>
</section>

</body>
</html>
```